Bright and beautiful business card for a coach

I'm a personal and business coach based in Perth, Australia. I need a business card that whilst subtle and elegant, will stand out and appeal on a table full of cards.

My business name is Fern Mentoring and the business card must represent the warmth and brightness implied in the name, without being gimmicky. It must have a warmth and appeal and be easy to read.

I prefer clean, minimalist designs.

It must align with the feel of my website and socials: https://www.fernmentoring-example.com.au/
https://www.instagram.com/fernmentoringau/
https://www.facebook.com/fernmentoringau
Updates

Hi Designers Thank you so much for taking the time to submit designs. I wonder if I could have explained myself a little better. Most of the designs that have been submitted look rather formal and many have quite corporate looking embellishments on them (to my eye). I would like softer, warmer, more organic. I’m open to people playing about and being more abstract, using softer embellishments (e.g the line drawing flowers and grasses I’ve used in my socials) incorporating other colours from my palette or like the social icons in my email signature (in PDF), perhaps playing with size/oversize, playing with the bleed. Please don’t be constrained by what I’ve already done, it merely needs to compliment. I’m sorry if I’m not using the right words or have led you astray. I’m no designer, but I’ve done my website, socials, email signature etc all myself (my logo was a design contest) and I was really hoping for my business card to be something more creative than I could have made with a template. Reminder: No black cards/sides please. Thank you 😊

Target Market(s)

Individuals, most likely but not all female. Creative thinkers. Likely professionals.

Industry/Entity Type

Business & Personal Coach

Contact Information for Business Card

(Fern Mentoring Logo) Name: Greta Pellham; Title: Business & Personal Coach; Phone number: +61 (0)458 913307; Email: greta@fernmentoring-example.com.au; Website: https://fernmentoring-example.com.au; Social icons for Facebook, Instagram & LinkedIn: @fernmentoringAU. Optional strapline: "A thinking partner to help you cut through the noise"

Font styles to use
Sans Serif

Colors
00AB8E
00BBA5
67D7C9
C6EFE9
E9F9F6
59FF00
82FF00
B8FF75
E3FFCB
F4FFEA
FFC000
F8CF3A
FAE287
FDF2CF
FEFAEE

Requirements
Must have
• Must align with feel of my website and socials. Must have a pop of #FFC000 (possibly whole of one side, or at least a block). Bright or white background. Easy to read.
Nice to have
• Possibly incorporate the sunshine/grass picture I have used in website and socials - will upload.
Should not have
• Must not be black or dark. Not impersonal or corporate looking.

```html
<!DOCTYPE html>
<html lang="en">
<head>
<meta charset="utf-8">
<title>Fern Mentoring – Business Card</title>
<link rel="stylesheet" href="https://fonts.googleapis.com/css2?family=Lato:wght@300;400&family=Great+Vibes&display=swap">
<style>
  :root {
    --sun: #FDC010;
    --white: #FFFFFF;
    --backdrop: #EDEBE6;
    --photo-green-light: #8DB255;
    --photo-green-deep: #5E8A37;
    --portrait-light: #D9CFC3;
    --portrait-deep: #B8A08A;
  }
  * { box-sizing: border-box; margin: 0; padding: 0; }
  html, body {
    width: 1200px; height: 1108px; overflow: hidden;
    background: var(--backdrop);
    font-family: "Lato", sans-serif;
  }
  .canvas {
    position: relative; width: 1200px; height: 1108px;
    display: flex; justify-content: center; align-items: center; gap: 40px;
  }
  .card {
    position: relative; width: 440px; height: 720px;
    background: var(--sun); border-radius: 26px; overflow: hidden;
    color: var(--white);
    box-shadow: 0 10px 30px rgba(0,0,0,0.12);
  }

  /* Front */
  .card-front { text-align: center; }
  .portrait {
    position: absolute; left: 100px; top: 62px; width: 240px; height: 280px;
    background: linear-gradient(180deg, var(--portrait-light) 0%, var(--portrait-deep) 100%);
  }
  .name {
    position: absolute; left: 0; right: 0; top: 360px;
    font-family: "Great Vibes", cursive; font-size: 56px; line-height: 1; font-weight: 400;
  }
  .title {
    position: absolute; left: 0; right: 0; top: 432px;
    font-size: 22px; line-height: 28px; font-weight: 400; letter-spacing: 0.3px;
  }
  .divider {
    position: absolute; left: 50px; right: 50px;
    display: flex; align-items: center; gap: 10px;
  }
  .divider::before, .divider::after {
    content: ""; flex: 1; height: 1px; background: var(--white);
  }
  .divider-contact { top: 476px; }
  .divider-social { top: 622px; }
  .icon-box {
    width: 34px; height: 34px; background: var(--white); border-radius: 5px;
    display: flex; align-items: center; justify-content: center;
  }
  .social-dot {
    width: 30px; height: 30px; border-radius: 50%; background: var(--white);
  }
  .contact-list {
    position: absolute; left: 0; right: 0; top: 524px;
    list-style: none; font-size: 19px; line-height: 28px; font-weight: 400;
  }
  .handle {
    position: absolute; left: 0; right: 0; top: 664px;
    font-size: 21px; line-height: 28px; font-weight: 400;
  }

  /* Back */
  .landscape {
    position: absolute; left: 0; top: 0; width: 440px; height: 410px;
    background: linear-gradient(180deg, var(--photo-green-light) 0%, var(--photo-green-deep) 100%);
  }
  .brand {
    position: absolute; left: 0; right: 0; top: 462px; text-align: center;
    font-size: 42px; line-height: 52px; font-weight: 300; letter-spacing: 2px;
  }
  .brand-mark {
    display: inline-block; width: 14px; height: 14px; border-radius: 50%;
    background: var(--white); margin-left: 10px; vertical-align: middle;
  }
  .strapline {
    position: absolute; left: 40px; right: 40px; top: 580px; text-align: center;
    font-size: 23px; line-height: 34px; font-weight: 400; text-transform: uppercase;
  }
</style>
</head>
<body>
<main class="canvas">

  <section class="card card-front" aria-label="Business card front">
    <div class="portrait" role="img" aria-label="Portrait photograph of Greta Pellham"></div>
    <h1 class="name">Greta Pellham</h1>
    <p class="title">Business &amp; Personal Coach</p>

    <div class="divider divider-contact">
      <span class="icon-box">
        <svg width="22" height="22" viewBox="0 0 24 24" aria-label="Phone"><path fill="#FDC010" d="M6.6 10.8a15.1 15.1 0 0 0 6.6 6.6l2.2-2.2c.3-.3.7-.4 1-.2 1.1.4 2.300.6 3.6.6.6 0 1 .4 1 1V20c0 .6-.4 1-1 1A17 17 0 0 1 3 4c0-.6.4-1 1-1h3.5c.6 0 1 .4 1 1 0 1.3.2 2.5.6 3.6.1.3 0 .7-.2 1z"/></svg>
      </span>
      <span class="icon-box">
        <svg width="22" height="22" viewBox="0 0 24 24" aria-label="Email"><rect x="3" y="5" width="18" height="14" rx="1.5" fill="none" stroke="#FDC010" stroke-width="2"/><path d="M3 6l9 7 9-7" fill="none" stroke="#FDC010" stroke-width="2"/></svg>
      </span>
      <span class="icon-box">
        <svg width="22" height="22" viewBox="0 0 24 24" aria-label="Website"><circle cx="12" cy="12" r="9" fill="none" stroke="#FDC010" stroke-width="2"/><path d="M3 12h18M12 3c3 3 3 15 0 18M12 3c-3 3-3 15 0 18" fill="none" stroke="#FDC010" stroke-width="1.6"/></svg>
      </span>
    </div>

    <ul class="contact-list">
      <li class="contact-phone">+61 (0)458 913307</li>
      <li class="contact-email">greta@fernmentoring-example.com.au</li>
      <li class="contact-web">www.fernmentoring-example.com.au</li>
    </ul>

    <div class="divider divider-social" aria-label="Social media">
      <span class="social-dot"></span>
      <span class="social-dot"></span>
      <span class="social-dot"></span>
    </div>
    <p class="handle">@fernmentoringAU</p>
  </section>

  <section class="card card-back" aria-label="Business card back">
    <div class="landscape" role="img" aria-label="Photograph of sunlight over long green grass"></div>
    <p class="brand">Fern Mentoring<span class="brand-mark"></span></p>
    <p class="strapline">A thinking partner to help you cut through the noise</p>
  </section>

</main>
</body>
</html>
```